Branding Pack for new business to business cost saving site

I would like a branding pack for my new project. I would like the following designed;
a4 Presentation folder
Letterhead
Envelope
Business Card
compliment splip

We are a business cost saving site, we have access to 1000s of discount offers for daily business to business offers. I already have the logo therfore please follow th e logo for the coloutr and design.

Target Market(s)

SMEs in United Kingdom

Industry/Entity Type

Business Service

Font styles to use
Serif
Script

Colors
0255a3
fbee3d

Requirements
Must have
• The folder needs to be the same size as attached

```html
<!DOCTYPE html>
<html lang="en">
<head>
<meta charset="utf-8">
<title>spendwise stationery set</title>
<link href="https://fonts.googleapis.com/css2?family=Montserrat:wght@400;600&display=swap" rel="stylesheet">
<style>
  :root {
    --navy: #333774;
    --navy-light: #3d4280;
    --yellow: #e9c94d;
    --paper: #f7f7f7;
    --backdrop: #d2d2d4;
    --ink-soft: #4a4e80;
  }
  * { box-sizing: border-box; margin: 0; padding: 0; }
  html, body { width: 1200px; height: 991px; overflow: hidden; }
  body {
    position: relative;
    background: var(--backdrop);
    font-family: "Montserrat", sans-serif;
    color: var(--navy);
  }
  .piece { position: absolute; overflow: hidden; }
  .wordmark {
    position: absolute;
    font-family: "Montserrat", sans-serif;
    font-weight: 400;
    letter-spacing: -0.02em;
    line-height: 1;
    display: flex;
    align-items: center;
    gap: 0.18em;
    white-space: nowrap;
  }
  .wordmark .dot {
    width: 0.28em; height: 0.28em;
    border-radius: 50%;
    background: var(--yellow);
  }
  .wordmark.on-navy { color: #ffffff; }
  .wordmark.on-paper { color: var(--navy); }
  .base-band {
    position: absolute; left: 0; right: 0; bottom: 0;
    height: 4px; background: var(--navy);
  }
  .accent-block {
    position: absolute; bottom: 0;
    height: 12px; background: var(--yellow);
  }
  .small-print {
    position: absolute;
    font-size: 5px;
    color: var(--ink-soft);
    white-space: nowrap;
  }

  /* Letterhead */
  .letterhead { left: 71px; top: 104px; width: 398px; height: 560px; background: var(--paper); }
  .letterhead .wordmark { left: 30px; top: 44px; font-size: 24px; }
  .letterhead .small-print { left: 30px; bottom: 14px; }
  .letterhead .accent-block { right: 48px; width: 56px; }

  /* Presentation folder */
  .folder {
    left: 507px; top: 90px; width: 432px; height: 575px;
    background: linear-gradient(135deg, var(--navy-light), var(--navy) 60%);
    border-radius: 3px;
  }
  .folder .spine {
    position: absolute; left: 26px; top: 0; bottom: 0;
    width: 1px; background: rgba(0,0,0,0.15);
  }
  .folder .wordmark { left: 179px; top: 78px; font-size: 38px; }
  .folder .sweep { position: absolute; left: 0; bottom: 0; width: 432px; height: 200px; }

  /* Business cards */
  .card-front { left: 66px; top: 696px; width: 170px; height: 94px; background: var(--paper); }
  .card-front .person { position: absolute; left: 16px; top: 22px; font-size: 5px; font-weight: 600; color: var(--navy); }
  .card-front .role { position: absolute; left: 16px; top: 29px; font-size: 4px; color: var(--ink-soft); }
  .card-front .wordmark { right: 14px; top: 18px; font-size: 15px; }
  .card-front .contact { position: absolute; left: 16px; top: 68px; font-size: 4px; line-height: 5.5px; color: var(--ink-soft); }
  .card-front .accent-block { right: 22px; width: 28px; height: 7px; bottom: 3px; }
  .card-front .base-band { height: 3px; }

  .card-back { left: 66px; top: 810px; width: 170px; height: 94px; background: var(--navy); }
  .card-back .wordmark { left: 14px; top: 24px; font-size: 15px; }
  .card-back .sweep { position: absolute; left: 0; bottom: 0; width: 170px; height: 40px; }

  /* Compliment slip */
  .slip { left: 266px; top: 696px; width: 415px; height: 208px; background: var(--paper); }
  .slip .wordmark { left: 22px; top: 32px; font-size: 24px; }
  .slip .small-print { left: 30px; bottom: 14px; }
  .slip .accent-block { right: 46px; width: 58px; height: 14px; }

  /* Envelope */
  .envelope { left: 718px; top: 696px; width: 415px; height: 208px; background: var(--paper); }
  .envelope .flap { position: absolute; left: 0; top: 0; width: 415px; height: 58px; }
  .envelope .wordmark { left: 50%; top: 24px; transform: translateX(-50%); font-size: 15px; }
</style>
</head>
<body>

  <section class="piece letterhead" aria-label="Letterhead">
    <div class="wordmark on-paper">spendwise<span class="dot"></span></div>
    <p class="small-print">Suite 2, 14 Harbour Rd, Bayview QLD 4870 · T: +61 7 4000 1234 · www.spendwise.co</p>
    <div class="accent-block"></div>
    <div class="base-band"></div>
  </section>

  <section class="piece folder" aria-label="Presentation folder">
    <div class="spine"></div>
    <div class="wordmark on-navy">spendwise<span class="dot"></span></div>
    <svg class="sweep" viewBox="0 0 432 200" preserveAspectRatio="none" aria-hidden="true">
      <path d="M0 110 C120 150 260 60 432 0 L432 200 L0 200 Z" fill="#2d3168"/>
      <path d="M0 124 C130 160 270 80 432 20 L432 200 L0 200 Z" fill="var(--yellow)"/>
    </svg>
  </section>

  <section class="piece card-front" aria-label="Business card front">
    <p class="person">JORDAN ELLERY</p>
    <p class="role">Director</p>
    <div class="wordmark on-paper">spendwise<span class="dot"></span></div>
    <p class="contact">Suite 2, 14 Harbour Rd, Bayview QLD 4870<br>T: +61 7 4000 1234 · E: info@spendwise.co<br>www.spendwise.co</p>
    <div class="accent-block"></div>
    <div class="base-band"></div>
  </section>

  <section class="piece card-back" aria-label="Business card back">
    <div class="wordmark on-navy">spendwise<span class="dot"></span></div>
    <svg class="sweep" viewBox="0 0 170 40" preserveAspectRatio="none" aria-hidden="true">
      <path d="M50 40 C90 30 140 20 170 4 L170 40 Z" fill="var(--yellow)"/>
    </svg>
  </section>

  <section class="piece slip" aria-label="Compliment slip">
    <div class="wordmark on-paper">spendwise<span class="dot"></span></div>
    <p class="small-print">Suite 2, 14 Harbour Rd, Bayview QLD 4870</p>
    <div class="accent-block"></div>
    <div class="base-band"></div>
  </section>

  <section class="piece envelope" aria-label="Envelope">
    <svg class="flap" viewBox="0 0 415 58" preserveAspectRatio="none" aria-hidden="true">
      <path d="M0 0 L415 0 L400 58 L15 58 Z" fill="var(--navy)"/>
    </svg>
    <div class="wordmark on-navy">spendwise<span class="dot"></span></div>
  </section>

</body>
</html>
```